I need a label design to go on our jars of honey. Our company is called Marrowdale Honey Co. The type of honey is called Fernlight Glen Honey. The jars are 1kg. Attached is the label size. Left hand side needs to have nutritional info... as attached. Middle section is our company name, honey type, 1kg & Whangamata, NZ. Right hand side needs to have info as per photo (raw honey etc). I would like to upload more pictures... but I’m unsure how to do this? Thanks, Carla

Target Market(s)

Honey consumers... families

Industry/Entity Type

Food Production

Colors

Designer to choose colors to be used in the design.

Requirements
Must have
• Nutritional info as per upload
• Type of honey & company name as per upload
• 1kg
• Address
Nice to have
• Similar fonts to upload.
• Possibly background image... floral or beach... very faint though.

```html
<!DOCTYPE html>
<html lang="en">
<head>
<meta charset="utf-8">
<title>Marrowdale Honey Co. – Jar Label, Right Panel</title>
<link rel="stylesheet" href="https://fonts.googleapis.com/css2?family=Inter:wght@300&display=swap">
<style>
  :root {
    --olive: #8a761c;
    --olive-deep: #7f6d1a;
    --petal: #d88a22;
    --petal-soft: #e39a2e;
    --ink: #ffffff;
  }
  html, body {
    margin: 0;
    padding: 0;
    width: 1200px;
    height: 1200px;
    overflow: hidden;
    background: var(--olive);
  }
  .label-panel {
    position: relative;
    width: 1200px;
    height: 1200px;
    background: radial-gradient(ellipse at 60% 50%, var(--olive) 0%, var(--olive-deep) 100%);
    font-family: "Inter", "Helvetica Neue", Arial, sans-serif;
    font-weight: 300;
    color: var(--ink);
    overflow: hidden;
  }
  .flower-photo {
    position: absolute;
    left: 0;
    top: 0;
    width: 320px;
    height: 1200px;
  }
  .copy {
    position: absolute;
    left: 400px;
    width: 704px;
    margin: 0;
    text-align: center;
    font-size: 42px;
    line-height: 52px;
    letter-spacing: -0.5px;
  }
  .copy--origin   { top: 86px; }
  .copy--raw      { top: 244px; }
  .copy--signoff  { top: 454px; }
  .copy--thanks   { top: 612px; }
  .copy--contact  { top: 876px; }
  .divider {
    position: absolute;
    left: 470px;
    top: 837px;
    width: 564px;
    height: 6px;
    background: var(--ink);
  }
</style>
</head>
<body>
  <main class="label-panel">
    <svg class="flower-photo" role="img" aria-label="Soft-focus photograph of an orange marigold flower at the left edge" viewBox="0 0 320 1200" xmlns="http://www.w3.org/2000/svg">
      <defs>
        <radialGradient id="bloom" cx="0" cy="0.5" r="1">
          <stop offset="0" stop-color="#e39a2e"/>
          <stop offset="0.7" stop-color="#d88a22"/>
          <stop offset="1" stop-color="#d88a22" stop-opacity="0"/>
        </radialGradient>
        <filter id="soften"><feGaussianBlur stdDeviation="14"/></filter>
      </defs>
      <ellipse cx="0" cy="600" rx="250" ry="480" fill="url(#bloom)" filter="url(#soften)"/>
    </svg>

    <p class="copy copy--origin">Sourced from the beautiful<br>Coromandel Peninsula.</p>
    <p class="copy copy--raw">Our honey comes to you raw &amp;<br>unpasteurised, ensuring it retains all<br>natural goodness!</p>
    <p class="copy copy--signoff">Arohanui,<br>Tomas, Carla &amp; boys</p>
    <p class="copy copy--thanks">‘Marrowdale’ all thanks to God for His<br>incredible creation!</p>

    <div class="divider"></div>

    <p class="copy copy--contact">www.marrowdalehoney.co.nz<br>42 Kowhai Lane<br>Whangamata, New Zealand</p>
  </main>
</body>
</html>
```